TLV Accounting Firm Needs Graphic Art for Our Proven Processes and For Our Core Values

**Looking for redesign of attached Powerpoint content (see below)
***Final graphic should be good for web use

Date: March 10, 2017

From: Colin Ashdown, CPA
Ashdown, Pettifer & Associates, P.C. (TLV)

Background:

TLV is a 20 person Houston based CPA firm, providing tax, accounting, financial and consulting services, to individuals and to entrepreneurs and their businesses. TLV is engaged in a process called KLU (See the book Headway, by Lars Obermeyer) whereby we implement a “system” to operate our company. As part of this system we have defined what we call our “Proven Process”. This is something we will show all prospective clients, and have on our website, that explains what it looks like to work with us. Starting at the beginning of the project to completion.

Project Description:

TLV is looking for graphic artist assistance in designing the following pieces:

1. Graphic depiction of “The TLV Way”, otherwise known as our “Proven Process”. The first attachments labeled TLV will show what we have done ourselves. These will show the general steps we have defined in both a sort of graphic way and a step by step narrative. The second attachment shows you some actual examples other firms have put together, hopefully that will show you what we are asking you to develop for us. Note that we are very open to any suggested clarifications or improvements to what we have done which may include changing phrases or saying something in a different way. Remember we are accountants!

2. We have defined our core values as a company, and we are wanting to develop some posters/placards so we can post them in our conference rooms, break room, etc. Attached are our core values as well as some deeper narratives about what they mean. Also included are many of the “words” we kicked around before arriving at our core values.

3. You will also find an attachment with our logo that should be incorporated, as well. Designs SHOULD INCLUDE, but not be limited to, the colors on our logo. Our end product should reflect a strong sense of our core values.

We would like to have the project in a form that would give us the option to use any/all of the information on our website, posters, brochures, etc.

Thanks in advance for your assistance.

Target Market(s)

Entrepreneurs and their companies with revenue greater than one million; Industries such as real estate, construction, trades and professional services; all in the Greater Houston Texas area

Industry/Entity Type

Accounting

Font styles to use
Serif
Other font styles liked:
• We are okay with Serif but are open.

Requirements
Must have
• Proven Process must be presented in a way that is clear and makes sense.
Nice to have
• Clean lines
• Colors should go with logo (see attached)
Should not have
• Can't think of anything - unless I see it

```html
<!DOCTYPE html>
<html lang="en">
<head>
<meta charset="utf-8">
<title>Client Service Approach – TLV</title>
<link rel="stylesheet" href="https://fonts.googleapis.com/css2?family=Open+Sans:wght@700;800&family=Source+Sans+3:wght@700&display=swap">
<style>
  :root {
    --header-top: #454545;
    --header-bottom: #232323;
    --white: #ffffff;
    --ink: #111111;
    --footer-start: #ffffff;
    --footer-end: #e4e4e4;
    --footer-rule: #cfcfcf;
    --brand-gold: #a8872f;
    --brand-gray: #4a4a4a;
    --step-red: #c8363f;
    --step-orange: #f47a3b;
    --step-yellow: #fde22f;
    --step-green: #9ccd55;
    --step-teal: #1daea5;
    --step-blue: #3eb1e2;
    --step-purple: #8b52a1;
  }
  * { margin: 0; padding: 0; box-sizing: border-box; }
  html, body { width: 1200px; height: 675px; overflow: hidden; background: var(--white); }
  .slide { position: relative; width: 1200px; height: 675px; overflow: hidden; background: var(--white); }

  .slide-header {
    position: absolute; left: 0; top: 0; width: 1200px; height: 65px;
    background: linear-gradient(90deg, var(--header-top), var(--header-bottom));
  }
  .slide-title {
    position: absolute; left: 29px; top: 10px;
    font-family: "Open Sans", sans-serif; font-weight: 800; font-size: 34px;
    color: var(--white); letter-spacing: 0.2px; line-height: 44px;
  }

  .process-chart { position: absolute; left: 0; top: 0; width: 1200px; height: 675px; }
  .step-title {
    font-family: "Open Sans", sans-serif; font-weight: 700; font-size: 14px;
    fill: var(--white); text-anchor: middle;
  }
  .step-note {
    font-family: "Source Sans 3", sans-serif; font-weight: 700; font-size: 10.5px;
    fill: var(--ink); text-anchor: middle;
  }

  .slide-footer {
    position: absolute; left: 0; top: 588px; width: 1200px; height: 87px;
    background: linear-gradient(90deg, var(--footer-start) 20%, var(--footer-end));
    border-top: 2px solid var(--footer-rule);
  }
  .firm-mark {
    position: absolute; left: 26px; top: 28px;
    display: flex; align-items: center; gap: 8px;
  }
  .firm-mark-square {
    width: 22px; height: 22px; background: var(--brand-gold);
  }
  .firm-name {
    font-family: "Open Sans", sans-serif; font-weight: 700; font-size: 14px;
    color: var(--brand-gray); line-height: 22px; white-space: nowrap;
  }
</style>
</head>
<body>
<main class="slide">
  <header class="slide-header">
    <h1 class="slide-title">CLIENT SERVICE APPROACH</h1>
  </header>

  <svg class="process-chart" viewBox="0 0 1229 691" preserveAspectRatio="none" aria-label="Client service process steps">
    <g class="step" transform="translate(53 0)">
      <polygon fill="var(--step-red)" points="0,205 142,205 226,342 173,429 31,429 84,342"/>
      <polygon fill="var(--step-red)" points="28,434 170,434 142,479 0,479"/>
      <text class="step-title" x="141" y="338">Philosophical</text>
      <text class="step-title" x="141" y="357">match</text>
      <text class="step-note" x="82" y="454">Initial meeting to</text>
      <text class="step-note" x="82" y="468">determine compatibility</text>
    </g>
    <g class="step" transform="translate(200 0)">
      <polygon fill="var(--step-orange)" points="0,205 142,205 226,342 173,429 31,429 84,342"/>
      <polygon fill="var(--step-orange)" points="28,434 170,434 142,479 0,479"/>
      <text class="step-title" x="145" y="338">Understand</text>
      <text class="step-title" x="145" y="357">your needs</text>
      <text class="step-note" x="87" y="454">Client questionnaire /</text>
      <text class="step-note" x="87" y="468">initial meeting</text>
    </g>
    <g class="step" transform="translate(348 0)">
      <polygon fill="var(--step-yellow)" points="0,205 142,205 226,342 173,429 31,429 84,342"/>
      <polygon fill="var(--step-yellow)" points="28,434 170,434 142,479 0,479"/>
      <text class="step-title" x="140" y="338">Philosophical</text>
      <text class="step-title" x="140" y="357">match</text>
      <text class="step-note" x="80" y="454">Initial meeting to</text>
      <text class="step-note" x="80" y="468">determine compatibility</text>
    </g>
    <g class="step" transform="translate(496 0)">
      <polygon fill="var(--step-green)" points="0,205 142,205 226,342 173,429 31,429 84,342"/>
      <polygon fill="var(--step-green)" points="28,434 170,434 142,479 0,479"/>
      <text class="step-title" x="143" y="338">Understand</text>
      <text class="step-title" x="143" y="357">your needs</text>
      <text class="step-note" x="85" y="454">Client questionnaire /</text>
      <text class="step-note" x="85" y="468">initial meeting</text>
    </g>
    <g class="step" transform="translate(643 0)">
      <polygon fill="var(--step-teal)" points="0,205 142,205 226,342 173,429 31,429 84,342"/>
      <polygon fill="var(--step-teal)" points="28,434 170,434 142,479 0,479"/>
      <text class="step-title" x="139" y="338">Philosophical</text>
      <text class="step-title" x="139" y="357">match</text>
      <text class="step-note" x="79" y="454">Initial meeting to</text>
      <text class="step-note" x="79" y="468">determine compatibility</text>
    </g>
    <g class="step" transform="translate(791 0)">
      <polygon fill="var(--step-blue)" points="0,205 142,205 226,342 173,429 31,429 84,342"/>
      <polygon fill="var(--step-blue)" points="28,434 170,434 142,479 0,479"/>
      <text class="step-title" x="142" y="338">Understand</text>
      <text class="step-title" x="142" y="357">your needs</text>
      <text class="step-note" x="85" y="454">Client questionnaire /</text>
      <text class="step-note" x="85" y="468">initial meeting</text>
    </g>
    <g class="step" transform="translate(938 0)">
      <polygon fill="var(--step-purple)" points="0,205 142,205 226,342 173,429 31,429 84,342"/>
      <polygon fill="var(--step-purple)" points="28,434 170,434 142,479 0,479"/>
      <text class="step-title" x="137" y="338">Philosophical</text>
      <text class="step-title" x="137" y="357">match</text>
      <text class="step-note" x="78" y="454">Initial meeting to</text>
      <text class="step-note" x="78" y="468">determine compatibility</text>
    </g>
  </svg>

  <footer class="slide-footer">
    <div class="firm-mark">
      <span class="firm-mark-square" aria-hidden="true"></span>
      <span class="firm-name">Ashdown, Pettifer &amp; Associates, PC</span>
    </div>
  </footer>
</main>
</body>
</html>
```